Business Card Design

Just looking for a good designs that looks good with our company logo. I'd like it to be simple and to the point. Just including contact information, our logo, and my name somewhere on the card so future clients know who they're contacting, and a couple services offered. The two images I attached are pictures of our logo. I don't care which color they they are, I just attached both images to give a reference of logo colors depending on the color of the card.
Names: Carl Whitby
Phone: 816-555-0147
Email: greenstripeyard@fernmail.test
Services offered:
Mowing
Fertilization
Aeration
Bed & tree maintenance
and more.
Business
Names: Carl Whitby
Phone: 816-555-0147
(no website)

```html
<!DOCTYPE html>
<html lang="en">
<head>
<meta charset="utf-8">
<title>Greenstripe Yard – Business Card</title>
<link rel="stylesheet" href="https://fonts.googleapis.com/css2?family=Exo+2:wght@400;500;600&display=swap">
<style>
  :root {
    --backdrop: #2b2b2e;
    --paper: #ffffff;
    --coral: #e8503a;
    --navy: #333a4d;
    --ink-light: #ffffff;
  }
  * { margin: 0; padding: 0; box-sizing: border-box; }
  html, body { width: 1200px; height: 821px; overflow: hidden; }
  body {
    background: var(--backdrop);
    font-family: "Exo 2", sans-serif;
    position: relative;
  }
  .card {
    position: absolute;
    top: 250px;
    width: 540px;
    height: 310px;
    background: var(--paper);
    overflow: hidden;
  }
  .card--front { left: 40px; }
  .card--back { left: 620px; }

  /* front */
  .coral-panel {
    position: absolute;
    left: 216px; top: 18px; right: 18px; bottom: 18px;
    background: var(--coral);
  }
  .divider {
    position: absolute;
    left: 214px; top: 0; bottom: 0;
    width: 3px;
    background: var(--navy);
  }
  .name {
    position: absolute;
    top: 34px;
    font-size: 25px;
    font-weight: 500;
    letter-spacing: 3px;
    text-transform: uppercase;
    line-height: 1;
    color: var(--navy);
  }
  .name--first { right: 336px; }
  .name--last { left: 228px; }
  .role {
    position: absolute;
    left: 228px; top: 66px;
    font-size: 11px;
    letter-spacing: 1.5px;
    text-transform: uppercase;
    color: var(--ink-light);
  }
  .contact-list { list-style: none; }
  .contact-item {
    position: absolute;
    left: 202px;
    right: 26px;
    display: flex;
    align-items: flex-start;
    gap: 14px;
    color: var(--ink-light);
    font-size: 13.5px;
    line-height: 1.3;
    letter-spacing: 0.5px;
  }
  .contact-item--address { top: 106px; }
  .contact-item--phone { top: 154px; }
  .contact-item--email { top: 188px; }
  .contact-item--services { top: 222px; }
  .contact-icon {
    flex: none;
    width: 26px; height: 22px;
    background: var(--coral);
    box-shadow: 2px 2px 0 rgba(0,0,0,0.35);
    display: flex; align-items: center; justify-content: center;
  }
  .contact-icon svg { width: 13px; height: 13px; }
  .contact-text { padding-top: 2px; }

  .brand {
    position: absolute;
    left: 20px; top: 176px;
    width: 180px;
    display: flex;
    flex-direction: column;
    align-items: center;
    gap: 10px;
  }
  .brand-dot {
    width: 44px; height: 44px;
    border-radius: 50%;
    background: var(--coral);
  }
  .brand-name {
    font-size: 22px;
    font-weight: 600;
    color: var(--navy);
    text-transform: uppercase;
    letter-spacing: 1px;
    text-align: center;
    line-height: 1.05;
  }

  /* back */
  .back-panel {
    position: absolute;
    inset: 18px;
    background: var(--navy);
  }
</style>
</head>
<body>
  <section class="card card--front" aria-label="Business card front">
    <div class="coral-panel"></div>
    <div class="divider"></div>

    <span class="name name--first">Carl</span>
    <span class="name name--last">Whitby</span>
    <span class="role">Lawn Care Specialist</span>

    <ul class="contact-list">
      <li class="contact-item contact-item--address">
        <span class="contact-icon">
          <svg viewBox="0 0 12 12"><path d="M6 1a3.5 3.5 0 0 0-3.5 3.5C2.5 7 6 11 6 11s3.5-4 3.5-6.5A3.5 3.5 0 0 0 6 1z" fill="#333a4d"/><circle cx="6" cy="4.5" r="1.3" fill="#e8503a"/></svg>
        </span>
        <span class="contact-text">412 Meadow Lane, Suite 8<br>Kansas City</span>
      </li>
      <li class="contact-item contact-item--phone">
        <span class="contact-icon">
          <svg viewBox="0 0 12 12"><path d="M3 1l2 2.5-1.2 1.2a6 6 0 0 0 3.5 3.5L8.5 7 11 9l-1.5 2C5 11 1 7 1 2.5z" fill="#333a4d"/></svg>
        </span>
        <span class="contact-text">816-555-0147</span>
      </li>
      <li class="contact-item contact-item--email">
        <span class="contact-icon">
          <svg viewBox="0 0 12 12"><rect x="1" y="2.5" width="10" height="7" fill="#333a4d"/><path d="M1 2.5l5 4 5-4" fill="none" stroke="#e8503a" stroke-width="1"/></svg>
        </span>
        <span class="contact-text">greenstripeyard@fernmail.test</span>
      </li>
      <li class="contact-item contact-item--services">
        <span class="contact-icon">
          <svg viewBox="0 0 12 12"><path d="M1.5 6.5l3 3 6-7" fill="none" stroke="#333a4d" stroke-width="2"/></svg>
        </span>
        <span class="contact-text">Mowing · Fertilization · Aeration<br>Bed &amp; tree maintenance and more</span>
      </li>
    </ul>

    <div class="brand">
      <span class="brand-dot"></span>
      <span class="brand-name">Greenstripe<br>Yard</span>
    </div>
  </section>

  <section class="card card--back" aria-label="Business card back">
    <div class="back-panel"></div>
  </section>
</body>
</html>
```